Very new and innovative Web design for Property managers of Vacation rentals

We are looking for a new website design for travel agencies and property managers specialised on vacation rentals business, holiday villas and apartments.

The end users of this website are travellers who are looking for a vacation home for their next holiday: this is the reason why the website must be easy to use, attractive, professional, possibly elegant and focused on get new reservations.

This is a draft of our current website: https://intro3.kelumsito.com/
Please consider that we would like to have proposals with a totally different and innovative layout, surprise us!

These are the pages of the website:
• Homepage: feel free to redesign all the homepage as you wish, surprise us with something very new! Please consider that Property manager/Travel agencies usually want to have the opportunity to put in evidence groups of houses with specific characteristics (eg. villas with private swimming pool, apartment in big/small towns, villas with air co, etc…), destinations and tourist areas, and sometimes experiences or activities (please consider that the website layout must be suitable even if some of the previous sections are not used).
• Search page: we’d like to organise the results of the search page in three different ways:
o Grid
o Map
o List
• Property page: to illustrate the characteristics, descriptions, images, …. of the property. It is very important to put in evidence images of the property and to maintain the booking form (and the other call to action bottom – eg. whatsapp) always visible
• Custom pages: static pages composed usually by text, images and call to actions
• Contact us (general form)
• Info request (specific of a property form)
• Booking process
• Blog, organised in four pages:
o Home Page – introduction to the blog
o List of articles
o Single article
o Site Map (presentation of categories and sub-categories)

If possible, we’d prefer to receive the material in Adobe XD or similar so that we can obtain the three versions:
- smartphone
- tablet
- desktop

The website will be then developed in Bootstrap: as a result we’ll need the icons in SVG format (or the library used)

In attachment you can find the map of the website pages

```html
<!DOCTYPE html>
<html lang="en">
<head>
<meta charset="utf-8">
<title>HavenStays – Property</title>
<link rel="stylesheet" href="https://fonts.googleapis.com/css2?family=Oswald:wght@300;400;500&family=Poppins:ital,wght@0,400;0,500;0,600;1,400&display=swap">
<style>
:root{
  --green:#12b583;
  --green-dark:#0d9a6e;
  --ink:#222;
  --muted:#666;
  --line:#e4e4e4;
  --footer:#1c1b1d;
  --white:#fff;
  --footer-text:#f2f2f2;
  --form-bg:#f4f7f6;
}
*{box-sizing:border-box;margin:0;padding:0}
html,body{width:1200px;height:2625px;overflow:hidden;background:var(--white)}
body{font-family:"Poppins",sans-serif;color:var(--ink);font-size:13px}
.page{position:relative;width:1200px;height:2625px;overflow:hidden}
.abs{position:absolute}
.head{font-family:"Oswald",sans-serif;font-weight:300;font-size:25px;color:var(--ink)}

/* header */
.brand{left:95px;top:20px;display:flex;align-items:center;gap:8px;font-size:25px;color:#555}
.brand .mark{width:34px;height:34px;background:var(--green);border-radius:50%}
.topbar{left:866px;top:0;width:334px;height:35px;background:var(--green);clip-path:polygon(0 0,100% 0,100% 100%,36px 100%);display:flex;align-items:center;justify-content:flex-end;gap:20px;padding-right:95px;color:#fff;font-size:10px;font-weight:600}
.nav{top:50px;right:96px;display:flex;gap:47px;font-size:11px;color:#444}
.nav .on{color:var(--green);font-weight:600}

/* hero */
.hero{left:0;top:94px;width:1200px;height:243px;background:linear-gradient(180deg,#3c3a36 0%,#6a6152 45%,#2f6f86 80%,#3a8fae 100%)}
.hero-title{left:0;width:1200px;top:240px;text-align:center;font-family:"Oswald",sans-serif;font-weight:500;font-size:40px;color:#fff}
.pill{left:94px;top:292px;width:118px;height:33px;border-radius:17px;background:#f2f2f2;font-family:"Oswald",sans-serif;font-size:14px;display:flex;align-items:center;justify-content:center}
.heart{left:1061px;top:284px;width:45px;height:45px;border-radius:50%;background:rgba(255,255,255,.35);display:flex;align-items:center;justify-content:center}

.crumbs{left:93px;top:367px;font-size:11px;color:#666}
.crumbs span{margin:0 6px;color:#999}
.crumbs b{font-weight:400;color:#222}

/* strip */
.shot{top:419px;height:263px}
.arrow{width:24px;height:24px;border-radius:50%;background:var(--green);top:540px;display:flex;align-items:center;justify-content:center}

/* property */
.title{left:93px;top:760px;font-family:"Oswald",sans-serif;font-weight:500;font-size:40px}
.type{left:94px;top:823px;font-style:italic;font-size:13px}
.specs{left:94px;top:842px;font-size:13px;color:var(--muted)}
.desc{left:93px;top:937px;width:660px;font-size:13px;line-height:21.6px;color:#555}

/* booking */
.book-shadow{left:797px;top:780px;width:319px;height:344px;background:var(--green)}
.book{left:788px;top:771px;width:320px;height:344px;background:var(--form-bg);border:1px solid #e8eceb}
.field{position:absolute;left:27px;width:263px;height:37px;border:1.5px solid #222;background:#fff;font-size:10.5px;display:flex;align-items:center;padding:0 12px;justify-content:space-between}
.field i{width:9px;height:9px;background:#222;display:block}
.btn-book{position:absolute;left:27px;top:238px;width:263px;height:37px;background:var(--green);color:#fff;font-size:12px;display:flex;align-items:center;justify-content:center}
.btn-info{position:absolute;left:27px;top:280px;width:263px;height:37px;background:#333;color:#fff;font-size:12px;display:flex;align-items:center;justify-content:center}

.share{left:634px;top:1088px;display:flex;gap:12px}
.share i{width:12px;height:12px;border-radius:50%;background:var(--green);display:block}

.amen{position:absolute;width:142px;height:38px;border-bottom:1px solid var(--line);display:flex;align-items:center;gap:8px;font-size:13px;color:#333}
.amen i{width:16px;height:14px;background:var(--green);border-radius:3px;display:block}

/* accommodations */
.acc{position:absolute;width:135px}
.acc-name{font-size:15px;color:var(--green);text-decoration:underline;text-underline-offset:4px}
.acc-row{display:flex;align-items:center;height:38px;border-bottom:1px solid var(--line);font-size:13px;color:#333;gap:8px}
.acc-row i{width:16px;height:14px;background:var(--green);display:block;border-radius:2px}
.acc-row b{font-weight:400;margin-left:auto;margin-right:22px}
.acc-btn{margin-top:10px;width:90px;height:34px;background:var(--green);color:#fff;font-size:12px;display:flex;align-items:center;justify-content:center}

/* footer */
.footer{left:0;top:2030px;width:1200px;height:595px;background:var(--footer)}
.f-brand{left:95px;top:2118px;display:flex;align-items:center;gap:10px;font-size:24px;font-weight:600;letter-spacing:1px;color:var(--footer-text)}
.f-brand .mark{width:40px;height:40px;border-radius:50%;background:var(--green)}
.sub{left:95px;top:2190px;font-size:12px;letter-spacing:1px;width:209px;padding-bottom:9px;border-bottom:2px solid #fff;color:var(--footer-text);font-weight:500}
.f-text{left:95px;top:2240px;width:300px;font-size:12px;letter-spacing:.8px;line-height:18px;color:#ddd}
.f-head{font-size:15px;color:var(--green);letter-spacing:1.5px;font-weight:500}
.f-links{left:518px;top:2143px;font-size:12px;letter-spacing:1px;line-height:34.6px;color:#eee}
.post{left:793px;display:flex;gap:10px;width:310px}
.post .thumb{width:70px;height:61px;flex:none}
.post h4{font-size:12px;color:var(--green);font-weight:600;line-height:15px}
.post p{font-size:12px;color:#eee;margin-top:10px}
.contact{top:2370px;height:117px;display:flex;align-items:center;gap:14px}
.contact h5{font-size:14px;color:var(--green);letter-spacing:1.5px;font-weight:600}
.contact p{font-size:14px;letter-spacing:1.2px;color:#eee}
.divider{top:2367px;width:1px;height:120px;background:#3a3a3c}
.legal{left:0;width:1200px;text-align:center;font-size:12px;letter-spacing:1px;font-weight:500;color:var(--footer-text)}
</style>
</head>
<body>
<div class="page">

  <!-- header -->
  <div class="abs brand"><span class="mark"></span>HavenStays</div>
  <div class="abs topbar"><span>LOGIN</span><span>WHISHLIST</span><span>EN</span></div>
  <nav class="abs nav"><span class="on">HOME</span><span>SEARCH</span><span>PROPERTY</span><span>CUSTOM</span><span>CONTACT US</span></nav>

  <!-- hero -->
  <div class="abs hero" role="img" aria-label="Evening photo of a modern villa with a pool"></div>
  <div class="abs hero-title">PROPERTY</div>
  <div class="abs pill">Photo Gallery</div>
  <div class="abs heart"><svg width="24" height="22" viewBox="0 0 24 22"><path d="M12 20 3 11a5 5 0 0 1 9-6 5 5 0 0 1 9 6z" fill="none" stroke="#fff" stroke-width="2"/></svg></div>

  <div class="abs crumbs">Home Page<span>/</span>Italy<span>/</span>Tuscany<span>/</span>Toscana<span>/</span>Casa Santa Rosa<span>/</span><b>Agriturismo La Quercia</b></div>

  <!-- photo strip -->
  <div class="abs shot" style="left:0;width:288px;background:linear-gradient(180deg,#b9c8d6,#d8d2c8 55%,#3aa7d1)" role="img" aria-label="Modern villa with palm trees and pool"></div>
  <div class="abs shot" style="left:303px;width:289px;background:linear-gradient(180deg,#8a7a64,#5d7a3e 60%,#6e6a60)" role="img" aria-label="Stone farmhouse terrace with climbing plants"></div>
  <div class="abs shot" style="left:605px;width:290px;background:linear-gradient(180deg,#b8cde0,#5f7f45 45%,#4fb3e6 75%,#b7aea2)" role="img" aria-label="Pool among green hills"></div>
  <div class="abs shot" style="left:909px;width:291px;background:linear-gradient(180deg,#7d9a52,#9c7a5c 50%,#5c4a3c)" role="img" aria-label="Stone house with garden and umbrella"></div>
  <div class="abs arrow" style="left:5px"><svg width="8" height="10"><path d="M6 1 2 5l4 4" stroke="#fff" stroke-width="2" fill="none"/></svg></div>
  <div class="abs arrow" style="left:1163px"><svg width="8" height="10"><path d="M2 1l4 4-4 4" stroke="#fff" stroke-width="2" fill="none"/></svg></div>

  <!-- property info -->
  <h1 class="abs title">Agriturismo La Quercia</h1>
  <div class="abs type">Country House / Farm House</div>
  <div class="abs specs">Accommodations: 2 Sleeps: 7 Bedrooms: 2 Bathrooms: 2</div>
  <h2 class="abs head" style="left:92px;top:895px">Description</h2>
  <p class="abs desc">il casale è immerson nella campagna toscana ma a soli 3 km dal paese più vicino dove potete trovare tutti i negozi con le principali comodità.<br>La piscina ad uso condiviso con i due appartamenti è di dimensioni 5*3 e profonda 1,30 mt , è recintata e aperta tutti i giorni dalle ore 09:00 alle ore 20:00.<br>è possibile affittare entrambi gli appartamenti per avere l'esclusività e la totale indipendenza.</p>

  <!-- booking form -->
  <div class="abs book-shadow"></div>
  <div class="abs book">
    <div class="field" style="top:26px">Accommodation<i></i></div>
    <div class="field" style="top:79px">Check In<i></i></div>
    <div class="field" style="top:132px">Check Out<i></i></div>
    <div class="field" style="top:183px;width:127px">Travelers<i></i></div>
    <div class="field" style="top:183px;left:163px;width:128px">Pets<i></i></div>
    <div class="btn-book">Book Now</div>
    <div class="btn-info">Info Request</div>
  </div>

  <!-- amenities -->
  <h2 class="abs head" style="left:92px;top:1075px">Amenities</h2>
  <div class="abs share"><i></i><i></i><i></i><i></i><i></i></div>
  <div class="abs" style="left:95px;top:1127px;width:142px;height:160px">
    <div class="amen" style="top:0"><i></i>Garden</div>
    <div class="amen" style="top:38px"><i></i>Baby Bed</div>
    <div class="amen" style="top:76px"><i></i>Swimmingpool</div>
    <div class="amen" style="top:114px;border-bottom:0"><i></i>Internet Wifi</div>
  </div>
  <div class="abs" style="left:360px;top:1127px;width:142px;height:120px">
    <div class="amen" style="top:0"><i></i>Near Village</div>
    <div class="amen" style="top:38px"><i></i>Maid</div>
    <div class="amen" style="top:76px;border-bottom:0"><i></i>Weedding</div>
  </div>
  <div class="abs" style="left:629px;top:1127px;width:142px;height:120px">
    <div class="amen" style="top:0"><i></i>Internet</div>
    <div class="amen" style="top:38px"><i></i>Parking</div>
    <div class="amen" style="top:76px;border-bottom:0"><i></i>Breakfast</div>
  </div>

  <!-- gallery -->
  <h2 class="abs head" style="left:92px;top:1312px">Gallery</h2>
  <div class="abs" style="left:94px;top:1358px;width:270px;height:166px;background:linear-gradient(180deg,#c6d3de,#dcd6cc 55%,#2fa1cf)" role="img" aria-label="Villa with pool"></div>

  <!-- accommodations -->
  <h2 class="abs head" style="left:527px;top:1312px">Accommodations</h2>
  <div class="acc" style="left:528px;top:1370px">
    <div class="acc-name">Casa Livia</div>
    <div style="height:13px"></div>
    <div class="acc-row"><i></i>Sleeps<b>4</b></div>
    <div class="acc-row"><i></i>Bed Room<b>1</b></div>
    <div class="acc-row" style="border:0"><i></i>Bathroom<b>1</b></div>
    <div class="acc-btn">View Details</div>
  </div>
  <div class="acc" style="left:745px;top:1370px">
    <div class="acc-name">Casa Serena</div>
    <div style="height:13px"></div>
    <div class="acc-row"><i></i>Sleeps<b>3</b></div>
    <div class="acc-row"><i></i>Bed Room<b>1</b></div>
    <div class="acc-row" style="border:0"><i></i>Bathroom<b>1</b></div>
    <div class="acc-btn">View Details</div>
  </div>

  <!-- map -->
  <div class="abs" style="left:94px;top:1622px;width:1013px;height:358px;background:linear-gradient(120deg,#b5d9a5 0%,#9fc7e8 35%,#c4dcaa 55%,#90c1ec 75%,#b9d9a4 100%)" role="img" aria-label="Map of Italy and the Adriatic showing the property location"></div>

  <!-- footer -->
  <div class="abs footer"></div>
  <div class="abs f-brand"><span class="mark"></span>HavenStays</div>
  <div class="abs sub">Subscribe to our Newsletter</div>
  <svg class="abs" style="left:325px;top:2208px" width="40" height="12"><path d="M0 6h38M32 1l6 5-6 5" stroke="#12b583" stroke-width="1.5" fill="none"/></svg>
  <p class="abs f-text">Our range of services is very large, and we are constantly expanding it.</p>

  <div class="abs f-head" style="left:516px;top:2102px">Navigation</div>
  <div class="abs f-links">Last Minute<br>Special Offers<br>Experience<br>Contact Us</div>

  <div class="abs f-head" style="left:792px;top:2102px">Recent posts</div>
  <div class="abs post" style="top:2145px">
    <div class="thumb" style="background:linear-gradient(180deg,#7c8f5a,#4d9bc8)" role="img" aria-label="Villa pool"></div>
    <div><h4>Which construction tool is better to choose?</h4><p>2 November, 2020</p></div>
  </div>
  <div class="abs post" style="top:2230px">
    <div class="thumb" style="background:linear-gradient(180deg,#8c6a4c,#2c7fb8)" role="img" aria-label="Terrace with ping pong table"></div>
    <div><h4>Which construction tool is better to choose?</h4><p>2 November, 2020</p></div>
  </div>

  <div class="abs contact" style="left:122px">
    <svg width="30" height="30" viewBox="0 0 24 24"><path d="M5 2l4 1 1 5-2 2a12 12 0 0 0 6 6l2-2 5 1 1 4-2 2C10 21 3 14 3 4z" fill="none" stroke="#12b583" stroke-width="1.8"/></svg>
    <div><h5>Call us</h5><p>+1 555 010 2290 (USA)</p></div>
  </div>
  <div class="abs divider" style="left:434px"></div>
  <div class="abs contact" style="left:485px">
    <svg width="40" height="30" viewBox="0 0 40 30"><rect x="1" y="1" width="38" height="28" rx="2" fill="none" stroke="#12b583" stroke-width="2"/><path d="M2 3l18 14L38 3" fill="none" stroke="#12b583" stroke-width="2"/></svg>
    <div><h5>Write to us</h5><p>hello@havenstays.test</p></div>
  </div>
  <div class="abs divider" style="left:763px"></div>
  <div class="abs contact" style="left:824px">
    <svg width="30" height="42" viewBox="0 0 30 42"><path d="M15 40C5 26 2 20 2 14a13 13 0 0 1 26 0c0 6-3 12-13 26z" fill="none" stroke="#12b583" stroke-width="2"/><circle cx="15" cy="14" r="5" fill="none" stroke="#12b583" stroke-width="2"/></svg>
    <div><h5>Office location</h5><p>12 Orchard Lane, Milford, NY 10001</p></div>
  </div>
  <div class="abs" style="left:94px;top:2487px;width:1013px;height:1px;background:#3a3a3c"></div>

  <div class="abs legal" style="top:2512px">Privacy Policies &nbsp; / &nbsp; Reservation Policies &nbsp; / &nbsp; Cookie Policy</div>
  <div class="abs legal" style="top:2530px">Copyright © 2021 HavenStays. All Rights Reserved. <span style="color:var(--green)">Powered by HavenStays</span></div>
  <div class="abs" style="left:578px;top:2567px;width:17px;height:17px;border-radius:50%;background:#fff"></div>
  <div class="abs" style="left:600px;top:2569px;width:55px;height:14px;border-radius:2px;background:#1877f2"></div>

</div>
</body>
</html>
```